Industry / Entity Type

Financial consultancy / advisers

Current site is: http://www.brightmoor-counsel.com

Looking for a complete overhaul of this site, we are after a clean modern look. Will require the ability to easily add, update and remove content, hence the WordPress design.
Example:
Add case studies
Industry documentation (downloadable brochures / flyers and such)

What we like from our current site is the colour the fonts and the logo (the city of London) we would like to have other city outlines (NYC and Tokyo, Hong Kong, Singapore).

The site will be used by our potential clients to get in contact and re-view the case studies, if possible would like to have a client login area where they can download our documents like NDA’s etc and T&C’s.

Task Outline

Create a Web Design (Coded - Design and coding required)
Designer must provide full implementation/coding depending on the platform chosen by the client (i.e. WordPress theme, HTML/CSS, bootstrap etc.)

Task Description

I need a full website built that must work on desktop and mobile. I can provide the London city skyline and the font file, which we have used. Some stock industrial photos will be required.

Requirements:

*Splash page
*What We Do
*How We do it
*Who Are We? To have the same information and links as the current site
*Why use us?
*Clients: To have the same information and links as the current site
*Partners: To have the same information and links as the current site
*Contact:

Target Market(s)

Financial institutions trading Equities, Futures, Options, Forex and Fixed Income.
Regulators, Exchanges, ECN’s
Buy side firms and Sell side firms

Industry/Entity Type

Financial

Coding

Coded - Design and coding required

Number of Pages Required

5+ page

Font styles to use
Sans Serif

Colors
f04a50

Requirements
Must have
• Splash page
• What We Do
• How We do it
• Who Are We? To have the same information and links as the current site
• Why use us?
• Clients: To have the same information and links as the current site
• Partners: To have the same information and links as the current site
• Contact:

```html
<!DOCTYPE html>
<html lang="en">
<head>
<meta charset="utf-8">
<title>Brightmoor Counsel</title>
<link rel="stylesheet" href="https://fonts.googleapis.com/css2?family=Michroma&family=Maven+Pro:wght@400;500;600&family=Open+Sans:wght@400;600&display=swap">
<style>
:root{
  --red:#f04a50;
  --ink:#222;
  --text:#555;
  --muted:#777;
  --light:#f3f3f3;
  --line:#d9d9d9;
  --white:#fff;
}
*{box-sizing:border-box;margin:0;padding:0}
html,body{width:1200px;height:2922px;overflow:hidden}
body{position:relative;background:var(--white);font-family:"Open Sans",Arial,sans-serif;color:var(--text)}
.display{font-family:"Michroma",Arial,sans-serif;font-weight:400;color:var(--ink);letter-spacing:2px}

/* hero */
.hero{position:absolute;left:0;top:0;width:1200px;height:549px;overflow:hidden}
.hero-bg{position:absolute;inset:0;background:linear-gradient(180deg,#1a2744 0%,#2f3f5e 30%,#5a5f72 55%,#8a6e5c 72%,#3a3a44 86%,#232732 100%)}
.hero-top{position:absolute;left:0;top:0;width:1200px;height:100px;background:rgba(10,18,36,.55);border-bottom:1px solid rgba(255,255,255,.15)}
.brand{position:absolute;display:flex;align-items:center;gap:10px;font-family:"Maven Pro",Arial,sans-serif;font-weight:500;letter-spacing:3px;color:var(--white);font-size:15px;text-transform:uppercase}
.brand .mark{width:12px;height:12px;border:2px solid currentColor}
.nav{position:absolute;top:40px;right:60px;display:flex;gap:22px;font-family:"Maven Pro",Arial,sans-serif;font-size:15px;color:var(--white)}
.nav .active{color:var(--red)}
.hero-title{position:absolute;left:0;width:1200px;top:200px;text-align:center;font-family:"Maven Pro",Arial,sans-serif;font-size:44px;letter-spacing:1px;color:var(--white);font-weight:400}
.hero-sub{position:absolute;left:0;width:1200px;top:268px;text-align:center;font-family:"Maven Pro",Arial,sans-serif;font-size:21px;line-height:32px;color:var(--white)}
.hero-btn{position:absolute;left:487px;top:358px;width:226px;height:42px;border-radius:21px;background:var(--red);border:2px solid #fff;color:#fff;font-family:"Maven Pro",Arial,sans-serif;font-size:16px;font-weight:600;text-align:center;line-height:38px;letter-spacing:.5px}
.dots{position:absolute;top:480px;left:565px;display:flex;gap:6px}
.dots span{width:13px;height:13px;border-radius:50%;border:2px solid #fff}
.dots span.on{background:#fff}

/* welcome */
.section-title{position:absolute;left:0;width:1200px;text-align:center;font-size:27px}
.intro{position:absolute;left:230px;width:740px;top:656px;text-align:center;font-size:12.5px;line-height:26px;color:var(--muted)}
.service{position:absolute;top:748px;width:263px;text-align:center}
.service svg{display:block;margin:0 auto}
.service h3{margin-top:44px;font-family:"Maven Pro",Arial,sans-serif;font-size:20px;font-weight:500;color:var(--ink);letter-spacing:.5px}
.service p{margin-top:10px;font-size:12.5px;line-height:22px;color:var(--muted)}

/* how */
.how{position:absolute;left:0;top:1038px;width:1200px;height:386px;background:var(--light)}
.how-photo{position:absolute;left:577px;top:0;width:623px;height:386px;clip-path:polygon(50px 0,100% 0,100% 100%,0 100%);background:linear-gradient(135deg,#151c2b 0%,#233a5c 40%,#2f78b0 62%,#1b2b45 85%,#0d1220 100%)}
.play{position:absolute;left:891px;top:1200px;width:62px;height:62px;border-radius:50%;background:#111}
.block-title{position:absolute;font-size:24px}
.copy{position:absolute;font-size:12.5px;line-height:25px;color:var(--text)}
.outline-btn{position:absolute;height:32px;border:1px solid #999;border-radius:16px;background:#fff;color:var(--red);font-family:"Maven Pro",Arial,sans-serif;font-size:12px;font-weight:600;text-align:center;line-height:30px;letter-spacing:.5px}

/* why */
.laptop-photo{position:absolute;left:58px;top:1500px;width:530px;height:305px;background:linear-gradient(180deg,#e9eaf0 0%,#c9ccd6 60%,#9ea2aa 100%)}
.ticks{position:absolute;left:651px;top:1568px;list-style:none}
.ticks li{display:flex;align-items:center;gap:14px;height:37px;font-size:13px;color:var(--text)}
.ticks li::before{content:"";width:15px;height:15px;border-radius:50%;background:var(--red);flex:none}
.tick-ico{position:absolute;left:651px}

/* testimonials */
.testimonials{position:absolute;left:0;top:1876px;width:1200px;height:407px;background:linear-gradient(120deg,#f35a60 0%,var(--red) 45%,#ec4650 100%)}
.quote{position:absolute;top:2013px;width:370px;text-align:center;color:#fff}
.avatar{width:98px;height:98px;border-radius:50%;margin:0 auto;border:3px solid #fff;background:linear-gradient(160deg,#d7d2cc,#9a948f)}
.quote p{margin-top:22px;font-size:13px;line-height:24px;padding:0 30px}
.quote p b{font-family:Georgia,serif;font-size:22px;margin-right:14px;vertical-align:-4px}
.quote .who{margin-top:14px;font-family:"Maven Pro",Arial,sans-serif;font-size:13.5px;line-height:22px;text-transform:uppercase}
.quote .role{font-family:"Maven Pro",Arial,sans-serif;font-size:13.5px}
.arrow{position:absolute;top:2061px;width:38px;height:38px;border-radius:50%;background:rgba(0,0,0,.22)}

/* partners */
.partner{position:absolute;top:2415px;width:179px;height:84px;border:3px solid #ddd;background:#fff}
.partner span{position:absolute;left:28px;right:28px;top:30px;height:18px;background:#cfcfcf;border-radius:2px}

/* footer */
.footer-rule{position:absolute;left:0;top:2565px;width:1200px;height:4px;background:var(--red)}
.f-title{position:absolute;top:2622px;font-family:"Maven Pro",Arial,sans-serif;font-size:17px;color:var(--ink);letter-spacing:1px}
.f-links{position:absolute;top:2658px;list-style:none;font-size:12.5px;line-height:20.5px;color:var(--text)}
.f-text{position:absolute;font-size:12.5px;line-height:22px;color:var(--text)}
.field{position:absolute;left:590px;top:2718px;width:255px;height:34px;border-bottom:1px solid #bbb;font-size:12px;color:#999;padding:8px 14px}
.contact-row{position:absolute;left:914px;display:flex;gap:18px;font-size:12.5px;line-height:22px;color:var(--text)}
.contact-row svg{flex:none;margin-top:4px}
.bottom-rule{position:absolute;left:97px;top:2840px;width:1006px;height:1px;background:var(--line)}
.copyright{position:absolute;left:97px;top:2872px;font-size:12.5px;color:var(--text)}
.socials{position:absolute;left:976px;top:2866px;display:flex;gap:10px}
.socials span{width:26px;height:26px;border-radius:50%;border:1px solid var(--red)}
</style>
</head>
<body>

<header class="hero">
  <div class="hero-bg" role="img" aria-label="Evening city harbour skyline with a lotus-shaped museum in the foreground"></div>
  <div class="hero-top"></div>
  <div class="brand" style="left:97px;top:40px"><span class="mark"></span>Brightmoor Counsel</div>
  <nav class="nav">
    <span class="active">Home</span><span>What we do</span><span>How we do it</span><span>Who are we</span><span>Why use us</span><span>Clients</span><span>Partners</span><span>Contact</span>
    <svg width="14" height="14" viewBox="0 0 14 14" style="margin-top:3px"><circle cx="6" cy="6" r="4.5" fill="none" stroke="#fff" stroke-width="2"/><line x1="9.2" y1="9.2" x2="13" y2="13" stroke="#fff" stroke-width="2"/></svg>
  </nav>
  <h1 class="hero-title">BRIGHTMOOR COUNSEL</h1>
  <p class="hero-sub">Provide solutions to solve potential issues to get you the correct solution<br>at the correct price point to achieve the desired results</p>
  <div class="hero-btn">GET MORE INFO &gt;&gt;</div>
  <div class="dots"><span class="on"></span><span></span><span></span><span></span></div>
</header>

<h2 class="section-title display" style="top:606px">Welcome to BMC</h2>
<p class="intro">Since founding Brightmoor Counsel in 2014 we have dedicated ourselves to the provision of services. What differentiates us from other advisers or consultancies is a genuine motivation to see our clients succeed.</p>

<div class="service" style="left:74px">
  <svg width="110" height="110" viewBox="0 0 110 110"><rect x="40" y="8" width="62" height="84" fill="var(--red)"/><rect x="50" y="24" width="42" height="5" fill="#fff"/><rect x="50" y="40" width="42" height="5" fill="#fff"/><rect x="50" y="56" width="42" height="5" fill="#fff"/><rect x="50" y="72" width="42" height="5" fill="#fff"/><circle cx="24" cy="40" r="13" fill="none" stroke="var(--red)" stroke-width="7"/><circle cx="30" cy="78" r="17" fill="none" stroke="var(--red)" stroke-width="8"/></svg>
  <h3>Data Management</h3>
  <p>At vero eos et accusamus et iustodi<br>dignissimos ducimus qui blan</p>
</div>
<div class="service" style="left:337px">
  <svg width="110" height="110" viewBox="0 0 110 110"><circle cx="55" cy="55" r="44" fill="none" stroke="var(--red)" stroke-width="14"/><rect x="36" y="60" width="9" height="16" fill="var(--red)"/><rect x="50" y="48" width="9" height="28" fill="var(--red)"/><rect x="64" y="36" width="9" height="40" fill="var(--red)"/></svg>
  <h3>Analytics</h3>
  <p>At vero eos et accusamus et iustodi<br>dignissimos ducimus qui blan</p>
</div>
<div class="service" style="left:600px">
  <svg width="120" height="110" viewBox="0 0 120 110"><path d="M10 50 a40 32 0 1 1 30 30 l-22 14 6-20 a40 32 0 0 1 -14 -24z" fill="var(--red)"/><circle cx="38" cy="50" r="6" fill="#fff"/><circle cx="58" cy="50" r="6" fill="#fff"/><circle cx="78" cy="50" r="6" fill="#fff"/></svg>
  <h3>Consulting</h3>
  <p>At vero eos et accusamus et iustodi<br>dignissimos ducimus qui blan</p>
</div>
<div class="service" style="left:863px">
  <svg width="110" height="110" viewBox="0 0 110 110"><circle cx="55" cy="55" r="26" fill="none" stroke="var(--red)" stroke-width="6"/><line x1="29" y1="55" x2="81" y2="55" stroke="var(--red)" stroke-width="4"/><ellipse cx="55" cy="55" rx="11" ry="26" fill="none" stroke="var(--red)" stroke-width="4"/><ellipse cx="55" cy="55" rx="50" ry="18" transform="rotate(35 55 55)" fill="none" stroke="var(--red)" stroke-width="6"/><ellipse cx="55" cy="55" rx="50" ry="18" transform="rotate(-35 55 55)" fill="none" stroke="var(--red)" stroke-width="6"/></svg>
  <h3>Trading</h3>
  <p>At vero eos et accusamus et iustodi<br>dignissimos ducimus qui blan</p>
</div>

<section class="how">
  <div class="how-photo" role="img" aria-label="Business person holding a tablet with rising financial charts"></div>
</section>
<div class="play"><svg width="62" height="62" viewBox="0 0 62 62"><path d="M25 19 L44 31 L25 43 Z" fill="#fff"/></svg></div>
<h2 class="block-title display" style="left:97px;top:1102px">How We Do It</h2>
<p class="copy" style="left:97px;top:1152px;width:450px">At vero eos et accusamus et iusto odio dignissimos ducimus qui blanditiis prasent ium voluptatum deleniti atque corrupti quo.</p>
<p class="copy" style="left:97px;top:1228px;width:450px">Dolores et quas molestias excepturi sint occaecati cupiditate non provident similiq ue sunt in culpa qui officia deserunt mollitia animi, id est laborum et dolorum fug t harum quidem rerum facilis est et expedita voluptas assumen est, omnis dolor epellend poribus autem quibusdam et aut officiis.</p>
<div class="outline-btn" style="left:97px;top:1357px;width:133px">READ MORE &gt;&gt;</div>

<div class="laptop-photo" role="img" aria-label="Laptop displaying a stock trading chart"></div>

<h2 class="block-title display" style="left:651px;top:1512px">Why Choose Us</h2>
<ul class="ticks">
  <li>At vero eos et accusamus et iusto odio dignissimos ducimus qui blaniis</li>
  <li>Praesentium voluptatum deleniti atque corrupti quos dolores et quas</li>
  <li>Excepturi sint occaecati cupiditate non provident, similiqt in culpa qui</li>
  <li>Nam libero tempore, cum soluta nobis est eligendi optio</li>
  <li>Dit quo minus id quod maxime placeat facere possimus, omnis volup</li>
</ul>
<svg class="tick-ico" style="top:1579px" width="15" height="185" viewBox="0 0 15 185">
  <g fill="none" stroke="#fff" stroke-width="2"><path d="M4 7.5l2.5 2.5 4.5-5"/><path d="M4 44.5l2.5 2.5 4.5-5"/><path d="M4 81.5l2.5 2.5 4.5-5"/><path d="M4 118.5l2.5 2.5 4.5-5"/><path d="M4 155.5l2.5 2.5 4.5-5"/></g>
</svg>
<div class="outline-btn" style="left:651px;top:1767px;width:144px">READ MORE &gt;&gt;</div>

<section class="testimonials"></section>
<h2 class="section-title display" style="top:1932px;color:#fff">Client Testimonials</h2>
<div class="quote" style="left:49px"><div class="avatar" role="img" aria-label="Client portrait"></div><p><b>&ldquo;</b>At vero eos et accusamus et iustodio dignissimos ducimus qui blanditiipraesnt ium voluptatum deleniti atque crupq</p><div class="who">Dana Whitlock</div><div class="role">Financial Services Professional</div></div>
<div class="quote" style="left:419px"><div class="avatar" role="img" aria-label="Client portrait"></div><p><b>&ldquo;</b>At vero eos et accusamus et iustodio dignissimos ducimus qui blanditiipraesnt ium voluptatum deleniti atque crupq</p><div class="who">Dana Whitlock</div><div class="role">Financial Services Professional</div></div>
<div class="quote" style="left:789px"><div class="avatar" role="img" aria-label="Client portrait"></div><p><b>&ldquo;</b>At vero eos et accusamus et iustodio dignissimos ducimus qui blanditiipraesnt ium voluptatum deleniti atque crupq</p><div class="who">Dana Whitlock</div><div class="role">Financial Services Professional</div></div>
<div class="arrow" style="left:30px"><svg width="38" height="38" viewBox="0 0 38 38"><path d="M22 12 L15 19 L22 26" fill="none" stroke="#fff" stroke-width="2.5"/></svg></div>
<div class="arrow" style="left:1132px"><svg width="38" height="38" viewBox="0 0 38 38"><path d="M16 12 L23 19 L16 26" fill="none" stroke="#fff" stroke-width="2.5"/></svg></div>

<h2 class="section-title display" style="top:2343px">Our Partners</h2>
<div class="partner" style="left:97px"><span></span></div>
<div class="partner" style="left:304px"><span></span></div>
<div class="partner" style="left:510px"><span></span></div>
<div class="partner" style="left:717px"><span></span></div>
<div class="partner" style="left:924px"><span></span></div>

<div class="footer-rule"></div>
<div class="brand" style="left:90px;top:2682px;color:var(--ink)"><span class="mark"></span>Brightmoor Counsel</div>

<h3 class="f-title" style="left:399px">Information</h3>
<ul class="f-links" style="left:399px"><li>Home</li><li>What we do</li><li>How we do it</li><li>Who are we</li><li>Why use us</li><li>Clients</li><li>Partners</li><li>Contact</li></ul>

<h3 class="f-title" style="left:590px">Newsletter Subscription</h3>
<p class="f-text" style="left:590px;top:2657px;width:230px">Register your Email Address to get information about us</p>
<div class="field">Email Address</div>
<div class="outline-btn" style="left:590px;top:2772px;width:96px;height:28px;line-height:26px;font-size:11px;border-radius:14px">SUBSCRIBE</div>

<h3 class="f-title" style="left:914px">Contact Us</h3>
<div class="contact-row" style="top:2662px"><svg width="10" height="14" viewBox="0 0 10 14"><path d="M5 0a5 5 0 0 1 5 5c0 4-5 9-5 9S0 9 0 5a5 5 0 0 1 5-5z" fill="var(--red)"/><circle cx="5" cy="5" r="2" fill="#fff"/></svg><span>Suite 4 Harrow Court,<br>Elmfield, Northbridge,<br>Hants, NB12 4QT</span></div>
<div class="contact-row" style="top:2746px"><svg width="12" height="12" viewBox="0 0 12 12"><path d="M2 0l3 3-1.5 1.5a8 8 0 0 0 4 4L9 7l3 3-2 2C5 12 0 7 0 2z" fill="var(--red)"/></svg><span>+1-555-010-0199</span></div>
<div class="contact-row" style="top:2784px"><svg width="13" height="10" viewBox="0 0 13 10"><rect width="13" height="10" fill="var(--red)"/><path d="M0 0l6.5 5L13 0" fill="none" stroke="#fff" stroke-width="1.2"/></svg><span>info@brightmoor-counsel.com</span></div>

<div class="bottom-rule"></div>
<p class="copyright">Copyrights &copy; 2017, Brightmoor Counsel. All rights reserved.</p>
<div class="socials"><span></span><span></span><span></span><span></span></div>

</body>
</html>
```